Automotive eCommerce Business looking for a business card design

Looking for a clean and simple business card design. Our company name is "Brindle Auto" and we are a company specializing in the ecommerce sales of automotive parts, specifically for pick up trucks and large SUVs. Our company colours are red, black, and white.

Feel free to use the logo provided or create a new logo that you seem fit. Looking forward to your creative ideas!

Industry/Entity Type

Automotive

Contact Information for Business Card

We were thinking of a possibly two-sided design featuring just the logo and company name on one side, and personal information on the other side. Single sided designs will be considered as well.

Font styles to use
Serif
Sans Serif
Decorative

Colors
ec1f27
ffffff
000000

Requirements
Must have
• Space for employee's name, title, phone number and email address, along with the company address and website somewhere.

```html
<!DOCTYPE html>
<html lang="en">
<head>
<meta charset="utf-8">
<title>Brindle Auto – Business Card</title>
<link rel="stylesheet" href="https://fonts.googleapis.com/css2?family=Cinzel:wght@400;500&family=Roboto:wght@400&display=swap">
<style>
  :root {
    --backdrop: #1f1f1f;
    --card-white: #f1f1f1;
    --brand-red: #9b1c20;
    --text-grey: #4a4a4a;
    --muted-grey: #6b6b6b;
    --divider: #8a8a8a;
    --white: #ffffff;
  }
  * { margin: 0; padding: 0; box-sizing: border-box; }
  html, body {
    width: 1200px; height: 960px; overflow: hidden;
    background: var(--backdrop);
  }
  .stage { position: relative; width: 1200px; height: 960px; }

  .card {
    position: absolute;
    width: 600px; height: 343px;
  }
  .card--front { left: 314px; top: 113px; background: var(--card-white); }
  .card--back  { left: 311px; top: 472px; background: var(--brand-red); }

  /* Front */
  .brand-mark {
    position: absolute; right: 42px; top: 86px;
    display: flex; align-items: center; gap: 10px;
    font-family: "Cinzel", serif; font-size: 22px; font-weight: 500;
    color: var(--brand-red); letter-spacing: 0.5px;
  }
  .brand-mark__square {
    width: 14px; height: 14px; background: var(--brand-red);
  }
  .person {
    position: absolute; left: 41px; top: 146px;
    font-family: "Cinzel", serif;
  }
  .person__name {
    font-size: 24px; font-weight: 500; color: var(--brand-red);
    line-height: 30px;
  }
  .person__title {
    font-size: 15px; color: var(--muted-grey); line-height: 18px;
  }
  .contacts {
    position: absolute; left: 41px; top: 214px;
    font-family: "Roboto", sans-serif; font-size: 14px;
    color: var(--text-grey); list-style: none;
  }
  .contacts li {
    display: flex; align-items: center; height: 19px;
  }
  .contacts svg {
    width: 13px; height: 13px; margin-right: 10px; fill: var(--brand-red);
    flex: none;
  }
  .address {
    position: absolute; left: 234px; top: 272px;
    padding-left: 21px; border-left: 1px solid var(--divider);
    font-family: "Roboto", sans-serif; font-size: 14px;
    color: var(--text-grey); line-height: 19px;
    font-style: normal;
  }

  /* Back */
  .back-square {
    position: absolute; left: 270px; top: 104px;
    width: 60px; height: 60px; background: var(--white);
  }
  .company-name {
    position: absolute; left: 0; right: 0; top: 228px;
    text-align: center;
    font-family: "Cinzel", serif; font-size: 26px; font-weight: 500;
    color: var(--white);
  }
  .company-site {
    position: absolute; left: 0; right: 0; top: 291px;
    text-align: center;
    font-family: "Roboto", sans-serif; font-size: 14px;
    letter-spacing: 5px; color: var(--white);
  }
</style>
</head>
<body>
<main class="stage">
  <section class="card card--front">
    <div class="brand-mark"><span class="brand-mark__square"></span>Brindle Auto</div>

    <div class="person">
      <h1 class="person__name">Owen Hartley</h1>
      <p class="person__title">CEO/Founder</p>
    </div>

    <ul class="contacts">
      <li>
        <svg viewBox="0 0 16 16" aria-hidden="true"><path d="M3.6 1l2.3 3-1.3 1.8c.9 2 2.5 3.6 4.6 4.6L11 9.1l3 2.3-1.2 2.9C7.5 14.5 1.5 8.5 1.7 3.2z"/></svg>
        555 210 4871
      </li>
      <li>
        <svg viewBox="0 0 16 16" aria-hidden="true"><path d="M4 0h8v16H4zM5.5 2v10h5V2zM7.2 13.2h1.6v1.4H7.2z" fill-rule="evenodd"/></svg>
        555 382 6150
      </li>
      <li>
        <svg viewBox="0 0 16 16" aria-hidden="true"><path d="M4 1h8v4H4zM1 6h14v6h-2v3H3v-3H1zM4.5 10v3.5h7V10z" fill-rule="evenodd"/></svg>
        555 947 3026
      </li>
      <li>
        <svg viewBox="0 0 16 16" aria-hidden="true"><path d="M1 3h14v10H1zM2.5 4.5L8 9l5.5-4.5v-.1h-11z"/></svg>
        owen@brindleauto.com
      </li>
      <li>
        <svg viewBox="0 0 16 16" aria-hidden="true"><circle cx="8" cy="8" r="7"/><path d="M5 4c1 1 2 1 2 3s-2 1-2 3M10 3c-1 2 1 3 2 3M9 12c0-2 2-2 3-1" stroke="#f1f1f1" stroke-width="1.2" fill="none"/></svg>
        www.brindleparts.com
      </li>
    </ul>

    <address class="address">
      1420 Harrow Ridge Road<br>
      Fairview, Oregon 97024
    </address>
  </section>

  <section class="card card--back">
    <span class="back-square" aria-hidden="true"></span>
    <h2 class="company-name">Brindle Auto Ltd.</h2>
    <p class="company-site">www.brindleauto.com</p>
  </section>
</main>
</body>
</html>
```